Etiketten-Design für Kaffeerösterei
Zielgruppe
Wir sind eine Kaffeerösterei. Zielgruppe: Kaffeetrinker von jung bis alt
Aufgabenstellung
Das fertige Etikett bzw. Grundgerüst soll abwandelbar sein und als Vorlage für viele verschiedene Sorten dienen. Farbliche Unterscheidung der Sorten wäre gewünscht (ca. 30 Sorten).
Pflichtangaben wie: (mindestens haltbar bis ende:.....) und EAN sowie das BIO Logo sollen noch auf dem Etikett Platz haben.
Gerne können unsere verschiedenen Sorten (aktueller Stand - ändern sich häufig) unter https://www.bol-tamers.de/da-kaffee/ sowie https://www.bol-tamers.de/da-esbresso/ einsehen.
Füllmenge und Firmenanschrift werden auf die Tüte gedruckt. Müssen somit nicht auf dem Etikett Platz finden.
Auf dem Bild ist die schwarze Verpackung (auf die wir umstellen möchten) und unser aktuelles Etikett abgebildet.
Etikettengröße: 105 (h) x 74 (b) mm

```html
<!DOCTYPE html>
<html lang="de">
<head>
<meta charset="utf-8">
<title>boltamers – Etiketten da röstla</title>
<link rel="stylesheet" href="https://fonts.googleapis.com/css2?family=Cabin:wght@500&family=Kalam:wght@400;700&family=Questrial&display=swap">
<style>
  :root {
    --bg: #ffffff;
    --ink: #1d1d1b;
    --brown: #4a2a1f;
    --blue: #1560ac;
    --green: #6cb52d;
    --label-bg: #ffffff;
    --label-shadow: rgba(0,0,0,0.22);
    --seal: #5aa82c;
  }
  * { box-sizing: border-box; margin: 0; padding: 0; }
  html, body { width: 1200px; height: 1200px; overflow: hidden; background: var(--bg); }
  .canvas { position: relative; width: 1200px; height: 1200px; }

  .brand { position: absolute; top: 120px; left: 0; width: 1200px; text-align: center; }
  .brand-name { font-family: 'Cabin', sans-serif; font-weight: 500; font-size: 78px; color: var(--ink); letter-spacing: -1px; line-height: 1; }
  .brand-rule { width: 260px; height: 2px; background: var(--ink); margin: 10px auto 8px; }
  .brand-sub { font-family: 'Cabin', sans-serif; font-weight: 500; font-size: 34px; color: var(--brown); letter-spacing: 6px; }

  .labels { position: absolute; top: 370px; left: 140px; display: flex; gap: 80px; }
  .label {
    width: 420px; height: 596px; background: var(--label-bg);
    box-shadow: 8px 8px 6px var(--label-shadow), 0 0 0 1px #e6e6e6;
    display: flex; flex-direction: column; align-items: center;
    padding-top: 30px; position: relative; overflow: hidden;
  }
  .label--blue { --accent: var(--blue); }
  .label--green { --accent: var(--green); }

  .label-brand { text-align: center; }
  .label-brand .name { font-family: 'Cabin', sans-serif; font-weight: 500; font-size: 38px; color: var(--ink); line-height: 1; letter-spacing: -0.5px; }
  .label-brand .rule { width: 172px; height: 1.5px; background: var(--ink); margin: 5px auto 3px; }
  .label-brand .sub { font-family: 'Cabin', sans-serif; font-weight: 500; font-size: 17px; color: var(--ink); letter-spacing: 2.6px; }

  .range { font-family: 'Kalam', cursive; font-size: 26px; color: var(--ink); margin-top: 14px; line-height: 1; }
  .variety { font-family: 'Kalam', cursive; font-weight: 700; font-size: 78px; color: var(--accent); line-height: 1; margin-top: 24px; }
  .content { font-family: 'Kalam', cursive; font-size: 26px; color: var(--ink); margin-top: 14px; line-height: 1; }

  .strength { display: flex; gap: 10px; margin-top: 22px; color: var(--ink); }
  .strength svg { width: 64px; height: 58px; }
  .strength .is-active { color: var(--accent); }

  .claim { font-family: 'Kalam', cursive; font-size: 18px; color: var(--accent); margin-top: 14px; white-space: nowrap; }

  .label-foot { position: absolute; left: 0; right: 0; bottom: 22px; display: flex; flex-direction: column; align-items: center; }
  .seal { align-self: flex-end; margin-right: 32px; width: 58px; height: 58px; border-radius: 50%; border: 4px solid var(--seal); }
  .bbd { font-family: 'Questrial', sans-serif; font-size: 15.5px; color: var(--ink); letter-spacing: 0.6px; margin-top: 18px; }
</style>
</head>
<body>
<svg width="0" height="0" style="position:absolute" aria-hidden="true">
  <defs>
    <symbol id="cup" viewBox="0 0 64 58">
      <g fill="none" stroke="currentColor" stroke-width="4.5" stroke-linecap="round" stroke-linejoin="round">
        <ellipse cx="28" cy="8" rx="17" ry="4"/>
        <path d="M11 9 L14 40 Q15 44 20 44 L36 44 Q41 44 42 40 L45 9"/>
        <path d="M45 17 Q56 16 55 24 Q54 31 43 30"/>
        <path d="M5 44 Q6 53 28 53 Q50 53 51 44"/>
      </g>
    </symbol>
  </defs>
</svg>

<main class="canvas">
  <header class="brand">
    <div class="brand-name">boltamers</div>
    <div class="brand-rule"></div>
    <div class="brand-sub">kaffeemanufaktur</div>
  </header>

  <section class="labels">
    <article class="label label--blue">
      <div class="label-brand">
        <div class="name">boltamers</div>
        <div class="rule"></div>
        <div class="sub">kaffeemanufaktur</div>
      </div>
      <p class="range">da röstla</p>
      <h2 class="variety">”lalomi”</h2>
      <p class="content">Röstkaffee 250g</p>
      <div class="strength" aria-label="Stärke 4 von 5">
        <svg><use href="#cup"/></svg>
        <svg><use href="#cup"/></svg>
        <svg><use href="#cup"/></svg>
        <svg class="is-active"><use href="#cup"/></svg>
        <svg><use href="#cup"/></svg>
      </div>
      <p class="claim">gut geröstet · fein gemahlen · frisch genossen</p>
      <div class="label-foot">
        <div class="seal" role="img" aria-label="Platz für Bio-Siegel"></div>
        <p class="bbd">mindestens haltbar bis ende: 00/00/2020</p>
      </div>
    </article>

    <article class="label label--green">
      <div class="label-brand">
        <div class="name">boltamers</div>
        <div class="rule"></div>
        <div class="sub">kaffeemanufaktur</div>
      </div>
      <p class="range">da röstla</p>
      <h2 class="variety">”zwoaradl”</h2>
      <p class="content">Röstkaffee 250g</p>
      <div class="strength" aria-label="Stärke 4 von 5">
        <svg><use href="#cup"/></svg>
        <svg><use href="#cup"/></svg>
        <svg><use href="#cup"/></svg>
        <svg class="is-active"><use href="#cup"/></svg>
        <svg><use href="#cup"/></svg>
      </div>
      <p class="claim">gut geröstet · fein gemahlen · frisch genossen</p>
      <div class="label-foot">
        <div class="seal" role="img" aria-label="Platz für Bio-Siegel"></div>
        <p class="bbd">mindestens haltbar bis ende: 00/00/2020</p>
      </div>
    </article>
  </section>
</main>
</body>
</html>
```